Car rental website design for a UAE car rental company

This project is about creating a new website design for a car rental company located in Dubai (United Arab Emirates), I opened the same project a few months ago but I didn't receive a lot of appealing entries so I closed it but this time I am marking the project as guaranteed to avoid such situation again, if you have already provided a design before then please re-submit again on this project so that it is considered while reviewing all the designs

A few important things:

1- We need a simple non-complex design
2- The final deliverable would be 2 screens (PSD, JPEG ... etc), the first screen is for the home page and the second screen is for an internal page
3- The home page must have a section that end users can use to rent a car online directly from the home page instead of going into some inner pages
4- The current website is very old and not very appealing so avoid creating a similar design (www.crestvane-autos.example)
5- The name is Crestvane but the company rents normal cars (no Limousin cars will be rented) so avoid adding any fancy cars in the images/graphics used in the design, just normal end users cars
6- The expected pages would be: home, About us, Our team, Strategy, Contact us and links to social media pages
7- The attachments include the company's logo and some screens from other car rental companies that provide online rentals/payments

If you have any questions please feel free to ask and please note that we will need the designs urgently

Thanks

Target Market(s)

Dubai - United Arab Emirates

Industry/Entity Type

It Company

Number of Pages Required

2 page

Font styles to use
Sans Serif

Requirements
Must have
• Check the project details
Nice to have
Should not have

```html
<!DOCTYPE html>
<html lang="en">
<head>
<meta charset="utf-8">
<title>Crestvane – Rent A Car</title>
<link href="https://fonts.googleapis.com/css2?family=Open+Sans:wght@300;400;600;700&display=swap" rel="stylesheet">
<style>
:root{
  --maroon:#a8003a;
  --maroon-dark:#8c0030;
  --orange:#f07800;
  --blue:#1ea6de;
  --yellow:#ffc000;
  --ink:#333333;
  --muted:#777777;
  --line:#dddddd;
  --footer:#333333;
  --footer-dark:#2a2a2a;
  --field:#ececec;
  --pink-field:#e9c6d1;
}
*{box-sizing:border-box;margin:0;padding:0}
html,body{width:1200px;height:2616px;overflow:hidden}
body{position:relative;font-family:"Open Sans",sans-serif;color:var(--ink);background:#fff}
.abs{position:absolute}

/* hero */
.hero{position:absolute;left:0;top:0;width:1200px;height:785px;overflow:hidden}
.hero-photo{position:absolute;inset:0;background:linear-gradient(180deg,#4d7a92 0%,#8fb3c4 22%,#c9d6d2 40%,#e8dcc0 50%,#8a9a9a 58%,#556b77 70%,#3a4a55 100%)}
.hero-car{position:absolute;left:205px;top:330px;width:440px;height:230px;border-radius:120px 150px 40px 40px;background:linear-gradient(180deg,#30b8d8,#0f6f8c)}
.navbar{position:absolute;left:0;top:35px;width:1200px;height:101px;background:rgba(30,50,65,.55)}
.brand{position:absolute;left:101px;top:44px;width:120px;text-align:center;color:#fff}
.brand-mark{display:block;width:44px;height:44px;margin:0 auto 4px;background:#fff;border:3px solid var(--maroon)}
.brand-name{font-size:20px;font-weight:600;line-height:22px}
.brand-tag{font-size:10px;font-weight:600;letter-spacing:1px}
.nav{position:absolute;top:70px;left:0;list-style:none}
.nav li{position:absolute;top:0;font-size:14px;font-weight:600;color:#fff;white-space:nowrap;line-height:28px}
.nav .active{background:var(--maroon);border:2px solid #fff;border-radius:5px;padding:0 20px;line-height:24px;box-shadow:0 0 0 2px var(--maroon)}
.search{position:absolute;left:1044px;top:70px}
.headline{position:absolute;right:100px;top:232px;text-align:right;color:#111;font-size:38px;font-weight:400;line-height:45px}
.arrow{position:absolute;top:317px;width:47px;height:48px;background:var(--maroon);display:flex;align-items:center;justify-content:center}

/* booking */
.booking{position:absolute;left:0;top:541px;width:1200px;height:244px;background:linear-gradient(180deg,rgba(150,10,45,.72),rgba(110,0,35,.92))}
.grab{position:absolute;left:98px;top:555px;width:200px;height:134px;background:var(--orange);color:#fff}
.grab:after{content:"";position:absolute;right:-16px;top:55px;border:16px solid transparent;border-left-color:var(--orange);border-right:0}
.grab-title{position:absolute;left:82px;top:46px;font-size:19px;line-height:20px}
.grab-sub{position:absolute;left:82px;top:69px;font-size:12px}
.manage{position:absolute;left:98px;top:694px;width:200px;height:61px;background:#8d9a96;color:#fff;font-size:11px;line-height:13px}
.manage span{position:absolute;left:58px;top:17px}
.label{position:absolute;font-size:14px;font-weight:600;color:#fff}
.field{position:absolute;height:30px;background:linear-gradient(#fff,#e3e3e3);border:1px solid #bbb}
.field.select:after{content:"";position:absolute;right:0;top:0;width:18px;height:28px;border-left:1px solid #bbb;background:linear-gradient(#f3f3f3,#dcdcdc)}
.btn{position:absolute;height:28px;font-size:10px;font-weight:600;display:flex;align-items:center;justify-content:center}
.btn-quote{left:773px;top:727px;width:157px;background:var(--blue);color:#fff}
.btn-world{left:945px;top:727px;width:155px;background:var(--yellow);color:#222}

/* featured */
.section-title{position:absolute;font-size:26px;font-weight:400;color:#222}
.section-title em{font-style:normal;color:var(--maroon)}
.rule{position:absolute;height:2px;background:#bbb}
.card{position:absolute;top:877px;width:231px;height:323px;border:1px solid var(--line);background:#fff}
.card-photo{position:absolute;left:9px;top:9px;width:213px;height:213px}
.card-name{position:absolute;left:18px;top:240px;width:190px;font-size:11px;line-height:17px;color:var(--maroon)}
.card-price{position:absolute;left:18px;top:282px;display:flex;gap:10px;align-items:center;font-size:16px}
.card-price .old{background:#e00000;color:#fff;padding:0 6px;line-height:22px}

/* testimonials */
.testimonials{position:absolute;left:0;top:1261px;width:1200px;height:488px;background:var(--maroon);color:#fff;text-align:center}
.t-title{position:absolute;top:48px;width:100%;font-size:44px;font-weight:400;letter-spacing:1px}
.t-quote{position:absolute;top:108px;width:100%;font-size:110px;font-weight:700;line-height:110px;font-family:Georgia,serif}
.t-head{position:absolute;top:215px;width:100%;font-size:24px;font-weight:600}
.t-body{position:absolute;left:105px;top:263px;width:990px;font-size:12.5px;line-height:17px}
.t-btn{position:absolute;left:546px;top:370px;width:106px;height:38px;border:2px solid #fff;font-size:12px;font-weight:600;line-height:34px}

/* brands */
.brands{position:absolute;left:99px;top:1859px;width:1001px;height:96px;display:flex;border:1px solid var(--line)}
.brand-cell{flex:1;border-right:1px solid var(--line);display:flex;align-items:center;justify-content:center}
.brand-cell:last-child{border-right:0}
.brand-cell i{display:block;width:50px;height:22px;background:#c9c9c9;border-radius:4px}

/* newsletter */
.newsletter{position:absolute;left:0;top:2018px;width:1200px;height:148px;background:var(--maroon-dark)}
.nl-label{position:absolute;left:99px;top:52px;font-size:25px;font-weight:600;color:#fff;letter-spacing:.5px}
.nl-input{position:absolute;top:50px;width:262px;height:47px;background:var(--pink-field);border:2px solid #d99bb0;font-size:13px;font-style:italic;color:#555;padding:13px 12px}
.nl-submit{position:absolute;left:954px;top:50px;width:146px;height:47px;background:var(--orange);color:#fff;font-size:18px;font-weight:600;display:flex;align-items:center;justify-content:center}

/* footer */
.footer{position:absolute;left:0;top:2166px;width:1200px;height:389px;background:var(--footer);color:#fff}
.f-col{position:absolute;top:28px}
.f-head{font-size:24px;font-weight:400;margin-bottom:22px}
.f-text{font-size:10.5px;line-height:24px}
.f-links{list-style:none;width:230px}
.f-links li{font-size:11px;line-height:33px;color:#ff4d7a;border-bottom:1px solid #444}
.f-links li:before{content:"- ";}
.tweet{font-size:11px;line-height:21px;width:230px;margin-bottom:14px}
.tweet b{color:var(--orange);font-weight:600}
.f-input{width:226px;height:35px;background:var(--footer-dark);font-size:12px;color:#999;padding:9px 14px;margin-bottom:9px}
.f-input.msg{height:80px}
.f-submit{width:74px;height:34px;background:var(--maroon);font-size:11px;font-weight:700;display:flex;align-items:center;justify-content:center}
.bottom{position:absolute;left:0;top:2555px;width:1200px;height:61px;background:var(--footer-dark);border-top:1px solid #444;color:#999;font-size:12px}
.bottom span{position:absolute;left:99px;top:22px}
</style>
</head>
<body>

<header class="hero">
  <div class="hero-photo" role="img" aria-label="Coastal mountain road at sunset with sunlit clouds"></div>
  <div class="hero-car" role="img" aria-label="Teal family sedan driving on the road"></div>
  <div class="navbar"></div>
  <div class="brand">
    <span class="brand-mark"></span>
    <div class="brand-name">Crestvane</div>
    <div class="brand-tag">Rent A Car</div>
  </div>
  <ul class="nav">
    <li class="active" style="left:511px">Home</li>
    <li style="left:607px">About</li>
    <li style="left:688px">Gallery</li>
    <li style="left:773px">Services</li>
    <li style="left:866px">News</li>
    <li style="left:942px">Contact</li>
  </ul>
  <svg class="search" width="30" height="30" viewBox="0 0 30 30" aria-label="Search"><circle cx="12" cy="12" r="8" fill="none" stroke="#fff" stroke-width="3"/><line x1="18" y1="18" x2="27" y2="27" stroke="#fff" stroke-width="3.5" stroke-linecap="round"/></svg>
  <h1 class="headline">Crestvane Drive is a really<br>best way to present your<br>beautiful mobile app</h1>
  <div class="arrow" style="left:0"><svg width="14" height="22" viewBox="0 0 14 22"><polyline points="11,2 3,11 11,20" fill="none" stroke="#fff" stroke-width="2.5"/></svg></div>
  <div class="arrow" style="left:1153px"><svg width="14" height="22" viewBox="0 0 14 22"><polyline points="3,2 11,11 3,20" fill="none" stroke="#fff" stroke-width="2.5"/></svg></div>
</header>

<section class="booking-panel">
  <div class="booking"></div>
  <div class="grab">
    <svg class="abs" style="left:8px;top:36px" width="68" height="62" viewBox="0 0 68 62" aria-hidden="true"><g fill="none" stroke="#fff" stroke-width="3"><path d="M20 8h24l6 12H14z"/><rect x="10" y="20" width="44" height="14" rx="3"/><path d="M10 34h0M8 44h22l5 10H4z"/><rect x="2" y="44" width="36" height="12" rx="3"/></g></svg>
    <div class="grab-title">Grab A Car</div>
    <div class="grab-sub">In Few Seconds</div>
  </div>
  <div class="manage">
    <svg class="abs" style="left:14px;top:12px" width="36" height="36" viewBox="0 0 36 36" aria-hidden="true"><rect x="4" y="2" width="24" height="30" fill="none" stroke="#fff" stroke-width="2.5"/><polyline points="10,18 15,23 24,12" fill="none" stroke="#fff" stroke-width="2.5"/></svg>
    <span>View Change or Cancel<br>A Car Reservation</span>
  </div>

  <div class="label" style="left:356px;top:551px">Pick up Location</div>
  <div class="field select" style="left:356px;top:572px;width:329px"></div>
  <div class="label" style="left:356px;top:628px">Pick-up Date &amp; Time *</div>
  <div class="field" style="left:356px;top:650px;width:165px"></div>
  <div class="field select" style="left:530px;top:650px;width:73px"></div>
  <div class="field select" style="left:612px;top:650px;width:73px"></div>
  <div class="label" style="left:356px;top:705px">Pick-up Date &amp; Time *</div>
  <div class="field select" style="left:356px;top:727px;width:329px"></div>

  <div class="label" style="left:773px;top:551px">Return Location</div>
  <div class="field select" style="left:773px;top:572px;width:327px"></div>
  <div class="label" style="left:773px;top:628px">Pick-up Date &amp; Time *</div>
  <div class="field" style="left:773px;top:650px;width:165px"></div>
  <div class="field select" style="left:946px;top:650px;width:70px"></div>
  <div class="field select" style="left:1028px;top:650px;width:72px"></div>
  <div class="btn btn-quote">GET A QUOTE</div>
  <div class="btn btn-world">Worldwide Booking</div>
</section>

<section class="featured">
  <h2 class="section-title" style="left:96px;top:817px">Featured <em>Cars</em></h2>
  <div class="rule" style="left:96px;top:857px;width:750px"></div>
  <h2 class="section-title" style="left:868px;top:807px">Specials</h2>
  <div class="rule" style="left:868px;top:857px;width:232px"></div>

  <article class="card" style="left:99px">
    <div class="card-photo" role="img" aria-label="White sports coupe in motion" style="background:linear-gradient(160deg,#6e6a62,#cfcfcf 55%,#5a554d)"></div>
    <div class="card-name">Consectetur adipisicing elit</div>
    <div class="card-price"><span class="old">$25,000</span><span>$23,750</span></div>
  </article>
  <article class="card" style="left:356px">
    <div class="card-photo" role="img" aria-label="Orange hatchback parked by the sea" style="background:linear-gradient(170deg,#8aa0b4,#c86a2a 60%,#6b6b6b)"></div>
    <div class="card-name">Mollitia quae laboriosam corporis delectus</div>
    <div class="card-price"><span>$38,999</span></div>
  </article>
  <article class="card" style="left:614px">
    <div class="card-photo" role="img" aria-label="Silver crossover SUV on a rocky road" style="background:linear-gradient(170deg,#3d5566,#a9b2b8 55%,#6f6a60)"></div>
    <div class="card-name">Non magni autem repellendus</div>
    <div class="card-price"><span class="old">$70,500</span><span>$64,860</span></div>
  </article>
  <article class="card" style="left:870px">
    <div class="card-photo" role="img" aria-label="Black compact coupe in a studio" style="background:linear-gradient(170deg,#c8d2da,#7b8a96 50%,#1e2226)"></div>
    <div class="card-name">Exercitationem voluptate beatae</div>
    <div class="card-price"><span class="old">$70,500</span><span>$66,975</span></div>
  </article>
</section>

<section class="testimonials">
  <h2 class="t-title">TESTIMONIALS</h2>
  <div class="t-quote">“</div>
  <h3 class="t-head">EU FUGIAT NULLA PARIATUR</h3>
  <p class="t-body">Lorem ipsum dolor sit amet conse ctetur adipisicing elit, sed do eiusmod tempor incididunt ut labore et dolore magna aliqua. Ut enim ad minim veniam, quis nostrud exercitation ullamco laboris nisi ut aliquip ex ea commodo consequat. Duis aute irure dolor in reprehenderit in voluptate velit esse cillum dolore eu fugiat nulla pariatur. Excepteur sint occaecat cupidatat non proident,.</p>
  <div class="t-btn">SEE ALL</div>
</section>

<section class="our-brands">
  <h2 class="section-title" style="left:97px;top:1808px">Our <em>Brands</em></h2>
  <div class="brands">
    <div class="brand-cell"><i></i></div><div class="brand-cell"><i></i></div><div class="brand-cell"><i></i></div><div class="brand-cell"><i></i></div><div class="brand-cell"><i></i></div>
    <div class="brand-cell"><i></i></div><div class="brand-cell"><i></i></div><div class="brand-cell"><i></i></div><div class="brand-cell"><i></i></div><div class="brand-cell"><i></i></div>
  </div>
</section>

<section class="newsletter">
  <div class="nl-label">Signup For Newsletter:</div>
  <div class="nl-input" style="left:401px">Email...</div>
  <div class="nl-input" style="left:675px">Phone Number...</div>
  <div class="nl-submit">Submit</div>
</section>

<footer class="footer">
  <div class="f-col" style="left:99px">
    <h3 class="f-head">Contact</h3>
    <p class="f-text">(Dubai Office / Head Office)<br>Level 4, Suite 402 / 18 Harbour Lane,<br>Al Qusais, Dubai<br>Phone: (04) 5550 118<br>(Deira Office)<br>Shop 3/210 Creek Road,<br>Deira, Dubai<br>(04) 5550 427</p>
  </div>
  <div class="f-col" style="left:358px">
    <h3 class="f-head">Quick Links</h3>
    <ul class="f-links">
      <li>Lorem ipsum dolor sit</li><li>Amet consectetur</li><li>Praesent vel sem id</li><li>Curabitur hendrerit est</li><li>Aliquam eget erat nec sapien</li><li>Cras id augue nunc</li><li>Sed a nulla urna</li>
    </ul>
  </div>
  <div class="f-col" style="left:612px">
    <h3 class="f-head">Latest Tweets</h3>
    <p class="tweet"><b>@namehere</b> Justoid nonummy laoreet phasellent penatoque in antesque pellus elis eget tincidunt. Nequatdui laoreet justo a non tellus laoreumt vitae doloreet<br>1 day ago</p>
    <p class="tweet"><b>@namehere</b> Justoid nonummy laoreet phasellent penatoque in antesque pellus elis eget tincidunt. Nequatdui laoreet justo a non tellus laoreumt vitae doloreet<br>1 day ago</p>
  </div>
  <div class="f-col" style="left:874px">
    <h3 class="f-head">Contact Us</h3>
    <div class="f-input">Full Name</div>
    <div class="f-input">Email Address</div>
    <div class="f-input">Subject</div>
    <div class="f-input msg">Message</div>
    <div class="f-submit">SUBMIT</div>
  </div>
</footer>
<div class="bottom"><span>Copyright © 2015 northpier.example - All Rights Reserved</span></div>

</body>
</html>
```